Retail Jewelry Business Card Design Project

We are in need of a new business card design for a retail jewelry store. This store is in the business of fine jewelry including but not specific to bridal jewelry, diamonds, designer jewelry and watches.

This store has been in business for 20 years but continues to strive for a modern professional appeal. The main colors use for this business are a royal blue, white and silver.

Target Market(s)

Target market is ages 18-50

Industry/Entity Type

Jewelry

Requirements
Must have
• Sales Person Name
Sales Person Email Address

Store Address
Store Phone
Website

Standard business card size. No odd shapes or sizes.
Nice to have
• Overall modern feel for card.

We have thought that a design with a nice feature of the logo on the back of the card would be nice but open to ideas.
Should not have
• No specific images of jewelry should be used.

```html
<!DOCTYPE html>
<html lang="en">
<head>
<meta charset="utf-8">
<title>Harlan Reed Fine Jewelry – Business Cards</title>
<link rel="stylesheet" href="https://fonts.googleapis.com/css2?family=Open+Sans:wght@400;600&family=Libre+Baskerville:ital,wght@1,700&display=swap">
<style>
  :root {
    --royal-blue: #2e3794;
    --white: #ffffff;
    --backdrop: #eceef3;
    --card-shadow: rgba(20, 24, 60, 0.18);
  }
  * { box-sizing: border-box; margin: 0; padding: 0; }
  html, body {
    width: 1200px;
    height: 751px;
    overflow: hidden;
    background: var(--backdrop);
    font-family: "Open Sans", Arial, sans-serif;
  }
  .stage {
    position: relative;
    width: 1200px;
    height: 751px;
  }
  .card {
    position: absolute;
    top: 226px;
    width: 520px;
    height: 298px;
    border-radius: 22px;
    overflow: hidden;
    box-shadow: 0 6px 18px var(--card-shadow);
  }
  .card--front { left: 50px; background: var(--white); }
  .card--back  { left: 630px; background: var(--royal-blue); color: var(--white); }

  /* Wordmark (invented name, one font, one weight, one colour) */
  .wordmark {
    position: absolute;
    left: 0; right: 0;
    text-align: center;
    font-family: "Open Sans", Arial, sans-serif;
    font-weight: 600;
    line-height: 1.1;
  }
  .wordmark__name { display: block; font-size: 46px; letter-spacing: 1px; }
  .wordmark__line { display: block; font-size: 22px; letter-spacing: 4px; text-transform: uppercase; }

  .card--front .wordmark { top: 40px; color: var(--royal-blue); }
  .card--back .wordmark  { top: 70px; color: var(--white); }

  /* Front: contact band */
  .contact-band {
    position: absolute;
    left: 0; right: 0;
    top: 172px;
    height: 90px;
    background: var(--royal-blue);
    color: var(--white);
  }
  .contact-band__address {
    position: absolute;
    right: 300px;
    top: 14px;
    text-align: right;
    font-size: 12.5px;
    line-height: 1.5;
  }
  .contact-band__divider {
    position: absolute;
    left: 232px;
    top: 6px;
    width: 1px;
    height: 50px;
    background: var(--white);
  }
  .contact-band__list {
    position: absolute;
    left: 246px;
    top: 4px;
    list-style: none;
    font-size: 12.5px;
    line-height: 1.45;
  }
  .contact-band__list li { display: flex; align-items: center; gap: 6px; }
  .contact-band__list svg { width: 10px; height: 10px; fill: var(--white); flex: none; }
  .contact-band__person {
    position: absolute;
    left: 0; right: 0;
    bottom: 6px;
    text-align: center;
    font-family: "Libre Baskerville", Georgia, serif;
    font-style: italic;
    font-weight: 700;
    font-size: 16px;
    letter-spacing: 1.5px;
  }

  /* Back */
  .card--back .wordmark__rule {
    display: block;
    width: 360px;
    height: 2px;
    margin: 6px auto 8px;
    background: var(--white);
  }
  .back__website {
    position: absolute;
    left: 0; right: 0;
    top: 222px;
    text-align: center;
    font-size: 13px;
    letter-spacing: 3px;
  }
</style>
</head>
<body>
<main class="stage">

  <section class="card card--front" aria-label="Business card front">
    <div class="wordmark">
      <span class="wordmark__name">Harlan Reed</span>
      <span class="wordmark__line">Fine Jewelry</span>
    </div>

    <div class="contact-band">
      <p class="contact-band__address">2280 Bayview Avenue<br>Lakeside Bay, FL 32000</p>
      <span class="contact-band__divider"></span>
      <ul class="contact-band__list">
        <li>
          <svg viewBox="0 0 10 10" aria-hidden="true"><path d="M2 0.5 L3.6 0.5 L4.2 2.8 L3 3.6 Q4 5.8 6.3 7 L7.2 5.8 L9.5 6.4 L9.5 8 Q9.5 9.5 8 9.5 Q0.5 9 0.5 2 Q0.5 0.5 2 0.5 Z"/></svg>
          555-014-2290
        </li>
        <li>
          <svg viewBox="0 0 10 10" aria-hidden="true"><path d="M0.5 2 L9.5 2 L9.5 8.5 L0.5 8.5 Z M1.2 2.6 L5 5.6 L8.8 2.6 Z" fill-rule="evenodd"/></svg>
          harlan@harlanreedjewelry.com
        </li>
        <li>
          <svg viewBox="0 0 10 10" aria-hidden="true"><path d="M5 0.3 A4.7 4.7 0 1 0 5 9.7 A4.7 4.7 0 1 0 5 0.3 Z M5 1.2 Q3.3 3 3.3 5 Q3.3 7 5 8.8 Q6.7 7 6.7 5 Q6.7 3 5 1.2 Z M1.3 4.5 L8.7 4.5 L8.7 5.5 L1.3 5.5 Z" fill-rule="evenodd"/></svg>
          www.harlanreedjewelry.com
        </li>
      </ul>
      <p class="contact-band__person">Harlan Reed Whitmore</p>
    </div>
  </section>

  <section class="card card--back" aria-label="Business card back">
    <div class="wordmark">
      <span class="wordmark__name">Harlan Reed</span>
      <span class="wordmark__rule"></span>
      <span class="wordmark__line">Fine Jewelry</span>
    </div>
    <p class="back__website">www.harlanreedjewelry.com</p>
  </section>

</main>
</body>
</html>
```